Business Management Fortress

Assist with enhancing a powerpoint slide by providing a few design options for consideration. I have a template but open to any creative ideas.

Internal employees and stakeholders

Business Management, Finance, Accounting

• Maintain a fortress, temple, or pyramid schema
• Scenic Background

```html
<!DOCTYPE html>
<html lang="en">
<head>
<meta charset="utf-8">
<title>Business Management Fortress</title>
<link href="https://fonts.googleapis.com/css2?family=Montserrat:wght@500;600&display=swap" rel="stylesheet">
<style>
  :root {
    --plum: #9b3566;
    --crimson: #dc3a55;
    --coral: #f96e40;
    --amber: #f6a01a;
    --rose-text: #e0405a;
    --fiduciary: #f26a3d;
    --side: #eef0fb;
    --side-dark: #dfe2f4;
    --ink: #111111;
    --bg: #ffffff;
  }
  * { margin: 0; padding: 0; box-sizing: border-box; }
  html, body { width: 1200px; height: 675px; overflow: hidden; background: var(--bg); }
  .slide {
    position: relative;
    width: 1200px; height: 675px;
    font-family: "Montserrat", sans-serif;
    font-weight: 500;
  }
  .frame {
    position: absolute;
    left: 7px; top: 9px; width: 1186px; height: 658px;
    border: 2px solid;
    border-image: linear-gradient(180deg, var(--amber), var(--plum)) 1;
  }
  .graphic { position: absolute; inset: 0; }
  .label {
    position: absolute;
    font-size: 15px;
    letter-spacing: 0.4px;
    line-height: 1;
    transform: translateY(-50%);
    white-space: nowrap;
  }
  .label.left { right: 1010px; text-align: right; }
  .label.right { left: 955px; }
  .plum { color: var(--plum); }
  .fid { color: var(--fiduciary); }
  .rose { color: var(--rose-text); }
  .amber { color: var(--amber); }
  .icon {
    position: absolute;
    width: 32px; height: 32px;
    border-radius: 6px;
    transform: translateY(-50%);
    opacity: 0.22;
  }
  .icon.left { left: 214px; }
  .icon.right { left: 901px; }
  .icon.plum { background: var(--plum); }
  .icon.fid { background: var(--fiduciary); }
  .icon.rose { background: var(--rose-text); }
  .icon.amber { background: var(--amber); }
  .slide-code {
    position: absolute;
    right: 16px; bottom: 14px;
    font-size: 12px; font-weight: 600;
    color: var(--ink);
  }
</style>
</head>
<body>
<div class="slide">
  <div class="frame"></div>

  <svg class="graphic" viewBox="0 0 1200 675" width="1200" height="675" aria-hidden="true">
    <defs>
      <linearGradient id="sideShade" x1="0" y1="0" x2="1" y2="0">
        <stop offset="0" stop-color="#f6f7fe"/>
        <stop offset="0.5" stop-color="#ffffff"/>
        <stop offset="1" stop-color="#e4e7f6"/>
      </linearGradient>
      <filter id="softShadow" x="-20%" y="-20%" width="140%" height="160%">
        <feDropShadow dx="0" dy="6" stdDeviation="8" flood-color="#8088b0" flood-opacity="0.25"/>
      </filter>
    </defs>

    <g class="pyramid" filter="url(#softShadow)">
      <!-- base layer -->
      <polygon fill="url(#sideShade)" points="392,340 567,434 741,340 741,392 567,488 392,392"/>
      <polygon fill="var(--amber)" points="567,247 741,340 567,434 392,340"/>
      <!-- third layer -->
      <polygon fill="url(#sideShade)" points="424,266 567,342 709,266 709,306 567,382 424,306"/>
      <polygon fill="var(--coral)" points="567,188 709,266 567,342 424,266"/>
      <!-- second layer -->
      <polygon fill="url(#sideShade)" points="451,200 567,256 681,200 681,230 567,290 451,230"/>
      <polygon fill="var(--crimson)" points="567,144 681,200 567,256 451,200"/>
      <!-- top layer -->
      <polygon fill="url(#sideShade)" points="475,134 567,186 659,134 659,158 567,212 475,158"/>
      <polygon fill="var(--plum)" points="567,83 659,134 567,186 475,134"/>
    </g>

    <g class="connectors" stroke="var(--ink)" stroke-width="1.3" fill="var(--ink)">
      <line x1="291" y1="150" x2="449" y2="150"/>
      <circle cx="291" cy="150" r="3.5"/><circle cx="449" cy="150" r="3.5"/>
      <line x1="289" y1="292.5" x2="402" y2="292.5"/>
      <circle cx="289" cy="292.5" r="3.5"/><circle cx="402" cy="292.5" r="3.5"/>
      <line x1="706" y1="208" x2="854" y2="208"/>
      <circle cx="706" cy="208" r="3.5"/><circle cx="854" cy="208" r="3.5"/>
      <line x1="770" y1="360.5" x2="854" y2="360.5"/>
      <circle cx="770" cy="360.5" r="3.5"/><circle cx="854" cy="360.5" r="3.5"/>
    </g>
  </svg>

  <!-- left column -->
  <span class="label left plum" style="top:97.5px">LEADER</span>
  <div class="icon left plum" style="top:95px" role="img" aria-label="Leader icon"></div>
  <span class="label left plum" style="top:150px">PARTNER</span>
  <div class="icon left plum" style="top:148px" role="img" aria-label="Handshake icon"></div>
  <span class="label left plum" style="top:202.5px">PROFITABILITY</span>
  <div class="icon left plum" style="top:202px" role="img" aria-label="Profit growth icon"></div>
  <span class="label left fid" style="top:285px">FIDUCIARY</span>
  <span class="label left fid" style="top:317.5px">RESPONSIBILITIES</span>
  <div class="icon left fid" style="top:301px" role="img" aria-label="Responsibility checklist icon"></div>

  <!-- right column, upper group -->
  <div class="icon right rose" style="top:81px" role="img" aria-label="People icon"></div>
  <span class="label right rose" style="top:82.5px">PEOPLE</span>
  <div class="icon right rose" style="top:134px" role="img" aria-label="Innovation icon"></div>
  <span class="label right rose" style="top:135px">INNOVATION</span>
  <div class="icon right rose" style="top:187px" role="img" aria-label="Business intelligence icon"></div>
  <span class="label right rose" style="top:187.5px">BUSINESS INTELLIGENCE</span>
  <div class="icon right rose" style="top:240px" role="img" aria-label="Strategic alliances icon"></div>
  <span class="label right rose" style="top:240px">STRATEGIC ALLIANCES</span>

  <!-- right column, lower group -->
  <div class="icon right amber" style="top:327px" role="img" aria-label="Financials icon"></div>
  <span class="label right amber" style="top:328px">ACCURATE FINANCIALS</span>
  <div class="icon right amber" style="top:379px" role="img" aria-label="Internal controls icon"></div>
  <span class="label right amber" style="top:380.5px">INTERNAL CONTROLS</span>
  <div class="icon right amber" style="top:432px" role="img" aria-label="Brand protection icon"></div>
  <span class="label right amber" style="top:433px">BRAND PROTECTION</span>
  <div class="icon right amber" style="top:485px" role="img" aria-label="Compliance icon"></div>
  <span class="label right amber" style="top:485.5px">COMPLIANCE</span>
  <div class="icon right amber" style="top:538px" role="img" aria-label="Ethics icon"></div>
  <span class="label right amber" style="top:538px">ETHICS</span>
  <div class="icon right amber" style="top:590px" role="img" aria-label="Cost management icon"></div>
  <span class="label right amber" style="top:591px">COST MANAGEMENT</span>

  <span class="slide-code">C63</span>
</div>
</body>
</html>
```